Merrow Trade finance web design

We are a newly established business which provides invoice finance to Small Businesses in England and Wales.
Our approach is very much a funder where the small business owner can talk to the decision maker. We will guarantee on receipt of information, a decision within 24 hours.
We are not a bank so the look of the website need to be friendly but professional.
Have two types of people we are trying to attract to the website: 1) partners who are small business owners and 2) introducers who is accountants and commercial brokers who introduce us to the small businesses.
Currently no website, although domain has been reserved.
The design should be:
Professional
“Clean” Look
Designed to convey Trust and Authority.
Appeal to the small business owner.
Must incorporate:
Logo (attached)
Front page:Top tabs to other pages 1) About us 2) Services 3) Introducers 4) Contact us
Need picture and logo on page.
1) About us page- Room for talk about the company, the people and our critera.
2) Services page- We need for what invoice finance is, and 5 boxes for different services we will provide. (link on page to contact us)
3) Introducers page- We need a part for why become an introducer? Who we can help? Why we are different? (link on page to contact us)
4) Contact us page- Office address, email, tel and if possible a map and a contact me part which will email direct to us.
Text will be provided for the design, if we can see the setup of the website we will provide a part for each of the pages to support.
Styles we think convey the correct image:
www.dornelcapital.example
www.plivanlend.example
www.quorbacredit.example
Target Market(s)
Small business owners
Industry/Entity Type
Finance
Number of Pages Required
5+ page
Look and feel

```html
<!DOCTYPE html>
<html lang="en">
<head>
<meta charset="utf-8">
<title>Merrow Trade Finance</title>
<link href="https://fonts.googleapis.com/css2?family=Open+Sans:wght@400;600&family=Poiret+One&family=Playfair+Display:ital@1&display=swap" rel="stylesheet">
<style>
:root{
  --red:#d7222a;
  --ink:#222;
  --body:#444;
  --muted:#777;
  --rule:#e2e2e2;
  --band:#2b2b2b;
  --footer:#ececec;
  --num:#d9d9d9;
}
*{margin:0;padding:0;box-sizing:border-box}
html,body{width:1200px;height:2299px;overflow:hidden;background:#fff}
body{position:relative;font-family:"Open Sans",Arial,sans-serif;color:var(--body)}
.abs{position:absolute}
.display{font-family:"Poiret One","Century Gothic",sans-serif;color:var(--ink);text-transform:uppercase;letter-spacing:1px}

/* header */
.brand{left:74px;top:22px;font-size:40px;font-weight:600;color:var(--red);letter-spacing:-1px;display:flex;align-items:center;gap:10px}
.brand-dot{width:16px;height:16px;border-radius:50%;background:var(--red)}
.support{left:760px;top:32px;width:207px;text-align:right;font-size:12.5px;line-height:18px;color:var(--ink)}
.phone-pill{left:980px;top:32px;width:145px;height:34px;border-radius:17px;background:var(--red);color:#fff;font-size:17px;text-align:center;line-height:34px}

/* nav */
.nav{left:0;top:98px;width:1200px;height:37px;border-top:1px solid #ddd;border-bottom:1px solid #ddd;background:#fff}
.nav-list{position:absolute;left:74px;top:0;display:flex;list-style:none;height:35px}
.nav-list li{font-size:12px;line-height:35px;padding:0 23px;color:var(--ink);text-transform:uppercase}
.nav-list li.active{background:var(--red);color:#fff;padding:0 28px}
.search{left:870px;top:0;width:255px;height:35px;background:#e9e9e9;font-size:12px;color:#777;line-height:35px;padding-left:32px}
.search svg{position:absolute;left:11px;top:11px}

/* hero */
.hero{left:0;top:135px;width:1200px;height:538px;background:linear-gradient(100deg,#d9d3cb 0%,#b9afa4 35%,#6f7e92 55%,#5a544d 75%,#3f3a35 100%)}
.hero-title{left:102px;top:278px;width:400px;font-size:22px;line-height:32px;color:#111;font-weight:400}
.hero-note{left:102px;top:398px;width:250px;font-size:15px;line-height:26px;color:var(--red);font-style:italic}
.hero-btn{left:102px;top:492px;width:181px;height:36px;border-radius:18px;background:var(--red);color:#fff;font-size:15px;text-align:center;line-height:36px}
.arrow{top:381px;width:48px;height:48px}

/* introducer band */
.band{left:0;top:673px;width:1200px;height:93px;background:var(--band)}
.band-text{left:72px;top:694px;width:730px;font-size:17px;line-height:24px;color:#fff}
.band-btn{left:855px;top:702px;width:228px;height:36px;border-radius:18px;background:var(--red);color:#fff;font-size:16px;text-align:center;line-height:36px}

/* services */
.section-title{left:0;width:1200px;text-align:center;font-size:29px;font-weight:400}
.section-sub{left:0;width:1200px;text-align:center;font-size:15px;color:var(--body)}
.services{left:74px;top:932px;width:1051px;height:250px;display:flex}
.service{flex:1;text-align:center;border-left:1px solid var(--rule);padding:0 12px}
.service:first-child{border-left:none}
.service svg{margin-top:6px;height:90px}
.service h3{font-weight:400;font-size:17px;color:var(--ink);margin-top:38px}
.service p{font-size:12.5px;line-height:20px;margin-top:10px;color:var(--body)}
.more{font-size:11.5px;color:var(--muted);margin-top:12px;display:inline-flex;align-items:center;gap:4px}
.circ{width:9px;height:9px;border:1px solid var(--muted);border-radius:50%;display:inline-block}
.hr{left:74px;width:1051px;height:1px;background:var(--rule)}

/* about */
.about-photo{left:74px;top:1330px;width:539px;height:310px;background:linear-gradient(110deg,#5b5f66 0%,#8a8f97 40%,#b7a48c 65%,#6a5a4a 100%)}
.about-frame{left:84px;top:1340px;width:519px;height:290px;border:2px solid #fff}
.about-title{left:669px;top:1325px;font-size:30px;font-weight:400}
.about-copy{left:669px;top:1374px;width:465px;font-size:12.8px;line-height:22.5px;color:var(--body)}
.about-copy p+p{margin-top:21px}
.about-more{left:669px;top:1603px}

/* why */
.why{top:1890px;width:340px;height:90px}
.why-num{position:absolute;left:0;top:-12px;font-family:"Playfair Display",Georgia,serif;font-style:italic;font-size:80px;color:var(--num);line-height:90px}
.why h3{position:absolute;left:100px;top:0;font-weight:400;font-size:17px;color:var(--ink);white-space:nowrap}
.why p{position:absolute;left:100px;top:30px;width:228px;font-size:12.5px;line-height:20px}

/* footer */
.footer{left:0;top:2053px;width:1200px;height:246px;background:var(--footer)}
.foot-head{font-size:18px;font-weight:400}
.foot-text{font-size:12.5px;line-height:20px;color:var(--body)}
.divider-v{left:600px;top:2088px;width:1px;height:112px;background:#d4d4d4}
.email-field{left:677px;top:2145px;width:313px;height:46px;background:#fff;font-size:12.5px;color:#888;line-height:46px;padding-left:18px}
.subscribe{left:1000px;top:2145px;width:125px;height:46px;background:var(--red);color:#fff;font-size:13px;text-align:center;line-height:46px;font-weight:600}
.foot-rule{left:74px;top:2236px;width:1051px;height:1px;background:#d4d4d4}
.social{left:920px;top:2251px;display:flex;gap:4px}
.social span{width:35px;height:35px;background:#c9c9c9;display:block}
</style>
</head>
<body>

<header>
  <div class="abs brand"><span class="brand-dot"></span>Merrow</div>
  <div class="abs support">Any Question? 24 hr Support<br>Call Us today!</div>
  <div class="abs phone-pill">1800 55 0142</div>
</header>

<nav class="abs nav">
  <ul class="nav-list">
    <li class="active">Home</li><li>About Us</li><li>Services</li><li>Introducers</li><li>Contact Us</li>
  </ul>
  <div class="abs search">
    <svg width="13" height="13" viewBox="0 0 13 13"><circle cx="5.5" cy="5.5" r="4.3" fill="none" stroke="#666" stroke-width="1.5"/><line x1="8.6" y1="8.6" x2="12" y2="12" stroke="#666" stroke-width="1.6"/></svg>
    Search
  </div>
</nav>

<section>
  <div class="abs hero" role="img" aria-label="Photo of a craftsman in glasses and denim shirt working at a bench in a workshop"></div>
  <h1 class="abs hero-title">Our approach is very much a funder where the small business owner can talk to the decision maker.</h1>
  <p class="abs hero-note">We will guarantee on receipt of information, a decision within 24 hours.</p>
  <div class="abs hero-btn">Contact Us Today!</div>
  <svg class="abs arrow" style="left:12px" viewBox="0 0 48 48"><circle cx="24" cy="24" r="22" fill="rgba(0,0,0,.35)" stroke="#fff" stroke-width="2"/><polyline points="27,15 18,24 27,33" fill="none" stroke="#fff" stroke-width="3"/></svg>
  <svg class="abs arrow" style="left:1139px" viewBox="0 0 48 48"><circle cx="24" cy="24" r="22" fill="rgba(0,0,0,.35)" stroke="#fff" stroke-width="2"/><polyline points="21,15 30,24 21,33" fill="none" stroke="#fff" stroke-width="3"/></svg>
</section>

<section>
  <div class="abs band"></div>
  <p class="abs band-text">Lorem Ipsum is simply dummy text of the printing and typesetting industry. Lorem Ipsum has been the industry's standard dummy text ever since the 1500s</p>
  <svg class="abs" style="left:775px;top:720px" width="75" height="32" viewBox="0 0 75 32"><path d="M2 22 Q30 34 66 16" fill="none" stroke="#999" stroke-width="1.5"/><polyline points="58,12 67,16 61,24" fill="none" stroke="#999" stroke-width="1.5"/></svg>
  <div class="abs band-btn">Become An Introducer</div>
</section>

<section>
  <h2 class="abs display section-title" style="top:812px">Services We Provide</h2>
  <p class="abs section-sub" style="top:862px">Lorem Ipsum has been the industry's standard dummy text ever since the 1500s.</p>
  <div class="abs services">
    <div class="service">
      <svg viewBox="0 0 90 90" width="90"><g fill="none" stroke="#888" stroke-width="2"><polyline points="8,62 30,40 46,52 78,18"/><polyline points="66,18 78,18 78,30"/><circle cx="44" cy="70" r="12"/><line x1="8" y1="84" x2="82" y2="84"/></g><text x="44" y="75" text-anchor="middle" font-size="14" fill="#888" font-family="Open Sans">$</text></svg>
      <h3>Service Title</h3>
      <p>Lorem Ipsum is simply dummy text standard dummy text ever has been the industry.</p>
      <span class="more"><i class="circ"></i>Read More</span>
    </div>
    <div class="service">
      <svg viewBox="0 0 90 90" width="90"><g fill="none" stroke="#888" stroke-width="2"><circle cx="36" cy="40" r="10"/><circle cx="36" cy="40" r="4"/><circle cx="58" cy="30" r="7"/><circle cx="58" cy="30" r="2.5"/><path d="M36 24v-4M36 56v4M20 40h-4M52 40h4"/><rect x="12" y="8" width="66" height="74" rx="10"/></g></svg>
      <h3>Service Title</h3>
      <p>Lorem Ipsum is simply dummy text standard dummy text ever has been the industry.</p>
      <span class="more"><i class="circ"></i>Read More</span>
    </div>
    <div class="service">
      <svg viewBox="0 0 90 90" width="90"><g fill="none" stroke="#888" stroke-width="2"><circle cx="32" cy="22" r="12"/><path d="M32 34v44"/><path d="M58 46a16 16 0 1 0 16 16h-16z"/><path d="M62 42a16 16 0 0 1 16 16h-16z"/></g></svg>
      <h3>Service Title</h3>
      <p>Lorem Ipsum is simply dummy text standard dummy text ever has been the industry.</p>
      <span class="more"><i class="circ"></i>Read More</span>
    </div>
    <div class="service">
      <svg viewBox="0 0 90 90" width="90"><g fill="none" stroke="#888" stroke-width="2"><rect x="26" y="8" width="54" height="36" rx="3"/><path d="M10 32h50v36H30l-12 12v-12h-8z"/><line x1="18" y1="44" x2="52" y2="44"/><line x1="18" y1="52" x2="52" y2="52"/><line x1="18" y1="60" x2="42" y2="60"/></g></svg>
      <h3>Service Title</h3>
      <p>Lorem Ipsum is simply dummy text standard dummy text ever has been the industry.</p>
      <span class="more"><i class="circ"></i>Read More</span>
    </div>
    <div class="service">
      <svg viewBox="0 0 90 90" width="90"><g fill="none" stroke="#888" stroke-width="2"><circle cx="45" cy="45" r="14"/><path d="M40 10h10l2 10 8 4 9-6 7 7-6 9 4 8 10 2v10l-10 2-4 8 6 9-7 7-9-6-8 4-2 10H40l-2-10-8-4-9 6-7-7 6-9-4-8-10-2V40l10-2 4-8-6-9 7-7 9 6 8-4z"/></g></svg>
      <h3>Service Title</h3>
      <p>Lorem Ipsum is simply dummy text standard dummy text ever has been the industry.</p>
      <span class="more"><i class="circ"></i>Read More</span>
    </div>
  </div>
  <div class="abs hr" style="top:1256px"></div>
</section>

<section>
  <div class="abs about-photo" role="img" aria-label="Photo of a small team talking around a meeting table in an office"></div>
  <div class="abs about-frame"></div>
  <h2 class="abs display about-title">About Our Company</h2>
  <div class="abs about-copy">
    <p>Lorem Ipsum is simply dummy text of the printing and typesetting industry. Lorem Ipsum has been the industry's standard dummy text ever since the 1500s, when an unknown printer took a galley of type and scrambled it to make a type specimen book.</p>
    <p>It was popularised in the 1960s with the release of transfer sheets containing Lorem Ipsum passages, and more recently with desktop publishing software and layout tools including versions of Lorem Ipsum.</p>
  </div>
  <span class="abs more about-more"><i class="circ"></i>More Information About Company</span>
  <div class="abs hr" style="top:1713px"></div>
</section>

<section>
  <h2 class="abs display section-title" style="top:1780px">Why We Are Different?</h2>
  <p class="abs section-sub" style="top:1828px">Lorem Ipsum has been the industry's standard dummy text ever since the 1500s.</p>
  <div class="abs why" style="left:74px"><span class="why-num">01</span><h3>Over 50 years of experience</h3><p>Lorem Ipsum has been the industry's took a galley of type it to make a type specimen book.</p></div>
  <div class="abs why" style="left:434px"><span class="why-num">02</span><h3>We fast, accuracy &amp; reliable</h3><p>Lorem Ipsum has been the industry's took a galley of type it to make a type specimen book.</p></div>
  <div class="abs why" style="left:794px"><span class="why-num">03</span><h3>We are improving everyday</h3><p>Lorem Ipsum has been the industry's took a galley of type it to make a type specimen book.</p></div>
</section>

<footer>
  <div class="abs footer"></div>
  <h4 class="abs display foot-head" style="left:74px;top:2096px">Get In Touch</h4>
  <p class="abs foot-text" style="left:74px;top:2136px">Merrow Trade Finance Limited<br>228, Lorem ipsum dolor,<br>Dosis anet - 84589</p>
  <p class="abs foot-text" style="left:345px;top:2136px">T: 1800 55 0142<br>E: info@merrowtrade.example</p>
  <div class="abs divider-v"></div>
  <h4 class="abs display foot-head" style="left:677px;top:2096px">Subscribe Our Newsletter</h4>
  <div class="abs email-field">Email Address</div>
  <div class="abs subscribe">SUBSCRIBE</div>
  <div class="abs foot-rule"></div>
  <p class="abs foot-text" style="left:74px;top:2259px">Copyright © 2016 Merrow Trade Finance Limited. All Rights Reserved</p>
  <p class="abs foot-text" style="left:801px;top:2259px">Connect With Us :</p>
  <div class="abs social" aria-label="Social links"><span></span><span></span><span></span><span></span><span></span></div>
</footer>

</body>
</html>
```